KVR - Redesign (PSD Files Only)

Requirements for the site:

1. We need our logo recreated, please use the same design and change colors to work on a white background

2. The site is a "Wizard" based site, that takes the customer through the process of creating a unique web presence that suits there needs

3.Colors Needed - Main "Dark Blue" Secondary = "Dark Grey" -Other = "Light Grey and White"

4.We need a CRISP CLEAN DESIGN, simple design

5.Wireframes are a general layout and may be modified by you to enhance the design

6. We want a complete web 5.0 look with big buttons and text boxes

7.The more personality the better

8. Current Site brightpolehub.example

9.See attachments for wireframes

10. Designer should deliver PSD files, no coding is required

11. The portfolio wireframe, should look like the design of the artflockly portfolio template
Updates

KEEP IT SIMPLE.,.....

We like the quillmark scaffold style of designs

```html
<!DOCTYPE html>
<html lang="en">
<head>
<meta charset="utf-8">
<title>KVR – Choose Maintenance Plan</title>
<link href="https://fonts.googleapis.com/css2?family=Dosis:wght@500;600;700&family=Open+Sans:ital,wght@0,400;0,600;1,400&display=swap" rel="stylesheet">
<style>
:root{
  --navy:#003763;
  --navy-deep:#002a4d;
  --ink:#111;
  --charcoal:#1c1c1c;
  --footer:#232323;
  --footer-deep:#1e1e1e;
  --page-grey:#d3d3d3;
  --rule:#e2e2e2;
  --orange-top:#ff8a1a;
  --orange-bot:#ff6a00;
  --white:#fff;
  --muted:#8a8a8a;
}
*{margin:0;padding:0;box-sizing:border-box}
html,body{width:1200px;height:1059px;overflow:hidden}
body{position:relative;background:var(--footer);font-family:"Open Sans",sans-serif;color:var(--ink)}
.abs{position:absolute}
.topstrip{left:0;top:0;width:1200px;height:24px;background:#151515}
.hero{left:0;top:23px;width:1200px;height:151px;background:radial-gradient(ellipse at 50% 90%,#0b5a92 0%,#07477a 40%,#033762 100%)}
.navbar{left:118px;top:0;width:964px;height:46px;background:var(--charcoal);clip-path:polygon(0 24px,11px 0,953px 0,964px 24px,964px 46px,0 46px)}
.logo{left:150px;top:7px;display:flex;align-items:center;gap:5px;color:#fff;font-family:"Dosis",sans-serif;font-weight:700;font-size:20px}
.logo i{width:10px;height:10px;background:#fff;display:block}
.nav a{position:absolute;top:0;height:46px;line-height:46px;color:#fff;font-family:"Dosis",sans-serif;font-weight:500;font-size:21px;text-decoration:none;text-align:center}
.nav .active{background:#0d4a7e}
.social-top span{position:absolute;top:10px;width:26px;height:26px;border-radius:50%;background:#fff}
.phone{display:flex;align-items:center;gap:4px;color:#fff;font-family:"Dosis",sans-serif;font-weight:500}
.step{left:0;width:1200px;text-align:center;color:#fff}
.step-no{top:70px;font-size:15px}
.step-title{top:88px;font-family:"Dosis",sans-serif;font-weight:600;font-size:35px;display:flex;justify-content:center;align-items:center;gap:16px}
.dots{letter-spacing:1px;font-size:18px;position:relative;top:-2px}
.step-sub{top:130px;font-size:16px}
.body-bg{left:0;top:174px;width:1200px;height:650px;background:var(--page-grey)}
.panel{left:129px;top:174px;width:942px;height:650px;background:var(--white)}
.notch{left:588px;top:162px;width:0;height:0;border-left:12px solid transparent;border-right:12px solid transparent;border-bottom:12px solid #fff}
.crumbs{left:171px;top:193px;font-size:12.5px;color:var(--navy);display:flex;gap:9px;align-items:center}
.crumbs .off{color:var(--muted)}
.crumbs b{font-weight:600;font-size:14px}
.crumb-rule{left:129px;top:225px;width:942px;height:1px;background:var(--rule)}
.gauge{left:798px;top:178px}
.opt-box{width:26px;height:26px;border:1px solid #bcbcbc;border-radius:3px;background:#fff;box-shadow:inset 0 1px 2px rgba(0,0,0,.08)}
.opt-box.on{border-color:#6d8fae}
.opt-title{font-size:14.5px;font-weight:600;color:var(--navy)}
.opt-text{font-size:12.3px;line-height:15px;color:var(--ink)}
.sep{left:162px;width:877px;height:2px;background:var(--rule)}
.cta{display:block;background:linear-gradient(var(--orange-top),var(--orange-bot));color:#fff;font-family:"Dosis",sans-serif;font-weight:600;font-size:27px;text-align:center;line-height:55px;border:1px solid #e55c00}
.cta-note{left:795px;top:590px;width:250px;font-size:15.5px;line-height:19px;color:var(--navy)}
.info{left:154px;top:733px;width:891px;height:51px;background:var(--navy);border:1px solid #0c4e85;display:flex;align-items:center;gap:11px;padding-left:16px;color:#fff;font-style:italic;font-size:15.5px}
.info-icon{width:28px;height:28px;border-radius:50%;background:#fff;color:var(--navy);font-family:Georgia,serif;font-weight:700;font-size:18px;display:flex;align-items:center;justify-content:center}
.foot-links{left:129px;top:866px;font-size:12.5px;line-height:19px;color:#fff}
.foot-social span{position:absolute;top:863px;width:38px;height:38px;border-radius:50%;background:#fff}
.badge-strip{left:129px;top:947px;width:948px;height:56px;background:var(--footer-deep)}
.badge{left:129px;top:948px;width:156px;height:53px;background:#fff;display:flex}
.badge i{width:54px;height:53px;background:#2d6fd8;display:block}
</style>
</head>
<body>
<div class="abs topstrip"></div>
<div class="abs hero"></div>
<header>
  <div class="abs navbar"></div>
  <div class="abs logo"><i></i>KVR</div>
  <nav class="nav">
    <a style="left:226px;width:64px">Home</a>
    <a class="active" style="left:295px;width:98px">About Us</a>
    <a style="left:398px;width:82px">Portfolio</a>
    <a style="left:485px;width:92px">Contact Us</a>
  </nav>
  <div class="social-top" aria-label="Social links">
    <span style="left:704px"></span><span style="left:738px"></span><span style="left:771px"></span><span style="left:805px"></span>
  </div>
  <div class="abs phone" style="left:884px;top:7px;font-size:25px">
    <svg width="14" height="20" viewBox="0 0 14 20"><path d="M3 1l3 4-2 2c1 3 3 6 5 7l2-2 3 3-2 3C6 18 0 10 1 3z" fill="#fff"/></svg>1800-555-0142
  </div>
</header>

<div class="abs step step-no">STEP 5</div>
<div class="abs step step-title"><span class="dots">•••••••</span>Choose Maintenance Plan<span class="dots">•••••••</span></div>
<div class="abs step step-sub">( Optional )</div>

<div class="abs body-bg"></div>
<main class="abs panel"></main>
<div class="abs notch"></div>

<div class="abs crumbs"><span>Level 1</span><b>»</b><span>Level 2</span><b>»</b><span>Level 3</span><b>»</b><span class="off">Level 4</span></div>
<div class="abs crumb-rule"></div>
<svg class="abs gauge" width="90" height="90" viewBox="0 0 90 90">
  <circle cx="45" cy="44" r="40" fill="#fff"/>
  <circle cx="45" cy="44" r="31" fill="none" stroke="#e3e3e3" stroke-width="13"/>
  <path d="M45 13 A31 31 0 0 0 16 34" fill="none" stroke="var(--navy)" stroke-width="13"/>
  <path d="M45 19 L47.5 44 L42.5 44Z" fill="#222"/>
  <circle cx="45" cy="44" r="4" fill="#9db3c8" stroke="#222" stroke-width="1.5"/>
</svg>

<section>
  <div class="abs opt-box on" style="left:165px;top:267px"><svg width="24" height="24" viewBox="0 0 24 24"><path d="M5 12l5 5 9-11" fill="none" stroke="var(--navy)" stroke-width="2.6"/></svg></div>
  <div class="abs opt-title" style="left:200px;top:265px">Allow Kavro Studios INC to host your website</div>
  <div class="abs opt-text" style="left:199px;top:283px;width:720px">Webhosting is required for all websites on the web. Our web hosting service is only $25 per month and includes discount on upgrades and&nbsp; progamming charges.</div>
  <div class="abs sep" style="top:332px"></div>

  <div class="abs opt-box" style="left:165px;top:357px"></div>
  <div class="abs opt-title" style="left:200px;top:355px">I will host my website</div>
  <div class="abs opt-text" style="left:199px;top:373px;width:560px">I am familiar with the web and will hire my own website hosting company to host my site. All upgrade and additional programming are at normal rates. (No. Savings)</div>
  <div class="abs sep" style="top:433px"></div>

  <div class="abs opt-box on" style="left:165px;top:457px"><svg width="24" height="24" viewBox="0 0 24 24"><path d="M5 12l5 5 9-11" fill="none" stroke="var(--navy)" stroke-width="2.6"/></svg></div>
  <div class="abs opt-title" style="left:200px;top:453px">I do not know what this means</div>
  <div class="abs opt-text" style="left:199px;top:471px">If you are unsure check this box and our consultants will consult with you and inform you of the pros and cons with wach plan.</div>
  <div class="abs sep" style="top:511px"></div>

  <a class="abs cta" style="left:795px;top:532px;width:244px;height:56px">Request Consultant</a>
  <p class="abs cta-note">Our web professionals will contact you to discuss your project</p>

  <div class="abs info"><span class="info-icon">i</span>As your full service marketing partner, we will deliver and end to end marketing solution for your business.</div>
</section>

<footer>
  <div class="abs foot-links">Home &nbsp;.&nbsp; About Us &nbsp;.&nbsp; Portfolio &nbsp;.&nbsp; Contact Us<br>Copyright © 2014 Kavro Studios Inc - All Right Reserved<br>brightpolehub.example</div>
  <div class="foot-social" aria-label="Social links">
    <span style="left:498px"></span><span style="left:544px"></span><span style="left:589px"></span><span style="left:635px"></span>
  </div>
  <div class="abs phone" style="left:498px;top:905px;font-size:25px">
    <svg width="14" height="20" viewBox="0 0 14 20"><path d="M3 1l3 4-2 2c1 3 3 6 5 7l2-2 3 3-2 3C6 18 0 10 1 3z" fill="#fff"/></svg>1800-555-0142
  </div>
  <a class="abs cta" style="left:828px;top:862px;width:244px;height:55px">Request Consultant</a>
  <div class="abs badge-strip"></div>
  <div class="abs badge" role="img" aria-label="Partner badge"><i></i></div>
</footer>
</body>
</html>
```